Redesign of business card for Cedar Ridge Mechanical

We are looking for a new design for our business cards for Cedar Ridge Mechanical. We are a plumbing & HVAC construction company, operating on the West Coast of Canada and USA. Logo attached.
Industry/Entity Type
Construction - Plumbing & HVAC
Contact Information for Business Card
Name, address, phone numbers, email, website address
Look and feel
Each slider illustrates characteristics of the customer's brand and the style your logo design should communicate.

```html
<!DOCTYPE html>
<html lang="en">
<head>
<meta charset="utf-8">
<title>Cedar Ridge Mechanical – Business Card</title>
<link rel="stylesheet" href="https://fonts.googleapis.com/css2?family=Open+Sans:wght@400;700&display=swap">
<style>
  :root {
    --bg: #c9c9c9;
    --card: #ffffff;
    --ink: #111111;
    --muted: #555555;
    --band-grey: #8a8a8a;
    --band-black: #000000;
  }
  html, body {
    margin: 0;
    padding: 0;
    width: 1200px;
    height: 896px;
    overflow: hidden;
    background: var(--bg);
    font-family: "Open Sans", sans-serif;
  }
  .canvas {
    position: relative;
    width: 1200px;
    height: 896px;
  }
  .card {
    position: absolute;
    left: 334px;
    width: 528px;
    height: 300px;
    background: var(--card);
    border-radius: 22px;
    overflow: hidden;
    box-shadow: 0 10px 18px rgba(0,0,0,0.18);
  }
  .card--front { top: 126px; }
  .card--back { top: 474px; height: 302px; }

  .brand {
    position: absolute;
    display: flex;
    align-items: center;
    gap: 12px;
    color: var(--ink);
    font-weight: 700;
    text-transform: uppercase;
    letter-spacing: 0.02em;
    white-space: nowrap;
  }
  .brand__square {
    background: var(--ink);
    flex: none;
  }
  .card--front .brand {
    left: 0; right: 0;
    top: 130px;
    justify-content: center;
    font-size: 27px;
  }
  .card--front .brand__square { width: 30px; height: 30px; }

  .card--back .brand {
    left: 36px;
    top: 120px;
    width: 220px;
    font-size: 15px;
    gap: 8px;
  }
  .card--back .brand__square { width: 18px; height: 18px; }

  .divider {
    position: absolute;
    left: 282px;
    top: 68px;
    width: 1.5px;
    height: 166px;
    background: var(--ink);
  }
  .contact {
    position: absolute;
    left: 300px;
    top: 62px;
    color: var(--muted);
    font-size: 14px;
    line-height: 19px;
  }
  .contact__name {
    margin: 0;
    color: var(--ink);
    font-size: 19px;
    font-weight: 700;
    line-height: 24px;
  }
  .contact__role { margin: 0 0 10px; }
  .contact__address { margin: 0 0 9px; }
  .contact__list {
    list-style: none;
    margin: 0;
    padding: 0;
    color: var(--ink);
  }
  .contact__list li {
    display: flex;
    align-items: center;
    gap: 6px;
    height: 19px;
  }
  .contact__list svg { width: 11px; height: 11px; flex: none; }

  .band {
    position: absolute;
    left: 0; right: 0; bottom: 0;
    height: 16px;
  }
</style>
</head>
<body>
<div class="canvas">

  <section class="card card--front">
    <div class="brand"><span class="brand__square"></span>Cedar Ridge Mechanical</div>
  </section>

  <section class="card card--back">
    <div class="brand"><span class="brand__square"></span>Cedar Ridge Mechanical</div>
    <div class="divider"></div>
    <div class="contact">
      <p class="contact__name">DANIEL MORROW</p>
      <p class="contact__role">Managing Director</p>
      <p class="contact__address">Your address, City<br>State, Zip 1234</p>
      <ul class="contact__list">
        <li><svg viewBox="0 0 24 24"><path fill="currentColor" d="M6.6 10.8a15 15 0 0 0 6.6 6.6l2.2-2.2a1 1 0 0 1 1-.25 11.4 11.4 0 0 0 3.6.57 1 1 0 0 1 1 1V20a1 1 0 0 1-1 1A17 17 0 0 1 3 4a1 1 0 0 1 1-1h3.5a1 1 0 0 1 1 1c0 1.25.2 2.45.57 3.57a1 1 0 0 1-.25 1z"/></svg>123 456 789</li>
        <li><svg viewBox="0 0 24 24"><rect x="6" y="2" width="12" height="20" rx="2" fill="none" stroke="currentColor" stroke-width="2.5"/><circle cx="12" cy="18" r="1.3" fill="currentColor"/></svg>123 456 789</li>
        <li><svg viewBox="0 0 24 24"><rect x="2" y="5" width="20" height="14" rx="1.5" fill="none" stroke="currentColor" stroke-width="2.5"/><path d="M2 6l10 7 10-7" fill="none" stroke="currentColor" stroke-width="2.5"/></svg>info@yourgmail.com</li>
        <li><svg viewBox="0 0 24 24"><circle cx="12" cy="12" r="10" fill="currentColor"/><path d="M2 12h20M12 2c3 3 3 17 0 20M12 2c-3 3-3 17 0 20" fill="none" stroke="#fff" stroke-width="1.5"/></svg>www.yourwebsite.com</li>
      </ul>
    </div>
    <svg class="band" viewBox="0 0 528 16" preserveAspectRatio="none" aria-hidden="true">
      <rect x="0" y="0" width="268" height="16" fill="var(--band-grey)"/>
      <polygon points="282,0 528,0 528,16 270,16" fill="var(--band-black)"/>
    </svg>
  </section>

</div>
</body>
</html>
```